Talbrook Answering Service Brochure

Design a brochure for an answering service/call center based on the information submitted/attached. Photos and text will be included. Would like it designed to complement the logo provided. This brochure will explain to the potential customer who we are and what we have to offer.

The Talbrook representatives take and processes inbound calls, 24-7-365

Target Market(s)

Any business, however, primarily Medical, oil and gas, non profits, and the service industry

Industry/Entity Type

Telecommunications

Font styles to use
Serif
Other font styles liked:
• coordinate with logo

Requirements
Must have
• Modern, bright, bold and neatly structured brochure that will complement the logo and our brand.

```html
<!DOCTYPE html>
<html lang="en">
<head>
<meta charset="utf-8">
<title>Talbrook Answering Service Brochure</title>
<link href="https://fonts.googleapis.com/css2?family=Questrial&display=swap" rel="stylesheet">
<style>
  :root {
    --backdrop: #d6d6d6;
    --charcoal: #323233;
    --charcoal-deep: #2a2a2b;
    --red: #d0111b;
    --red-deep: #a40c14;
    --white: #ffffff;
    --ink-soft: #e9e9e9;
    --rule: #6a6a6a;
    --photo-light: #e8e8ea;
    --photo-mid: #c9c9cd;
  }
  * { box-sizing: border-box; margin: 0; padding: 0; }
  html, body { width: 1200px; height: 978px; overflow: hidden; }
  body {
    background: var(--backdrop);
    font-family: "Questrial", "Century Gothic", sans-serif;
    color: var(--ink-soft);
  }
  .spread {
    position: absolute;
    left: 40px; top: 59px;
    width: 1120px; height: 860px;
    display: flex;
  }
  .page {
    position: relative;
    width: 560px; height: 860px;
    background: var(--charcoal);
    overflow: hidden;
  }
  .page-art { position: absolute; inset: 0; }
  .block { position: absolute; font-size: 11.4px; line-height: 1.38; }
  .block p { margin-bottom: 8px; }
  .label {
    display: inline-block;
    background: var(--red);
    color: var(--white);
    font-size: 15px;
    line-height: 1.2;
    padding: 3px 14px 3px 7px;
    border-radius: 0 5px 5px 0;
    margin-bottom: 8px;
  }
  .label.wide { display: block; border-radius: 5px; padding: 4px 8px; }
  .ticks { list-style: none; margin-top: 4px; }
  .ticks li { position: relative; padding-left: 18px; margin-bottom: 2px; }
  .ticks li::before { content: "\2713"; position: absolute; left: 0; top: 0; color: var(--ink-soft); }
  .col-rule { position: absolute; width: 1px; background: var(--rule); }
  .contact-heading { font-size: 19px; color: var(--white); text-align: center; }
  .web-tab {
    position: absolute; left: 30px; bottom: 0;
    width: 225px; height: 28px;
    background: var(--red);
    color: var(--white);
    font-size: 15px; font-weight: bold;
    display: flex; align-items: center; justify-content: center;
    border-radius: 6px 6px 0 0;
  }
  .list-title { font-size: 16px; color: var(--white); font-weight: bold; margin: 4px 0 2px; }
</style>
</head>
<body>
<main class="spread">

  <section class="page page-left">
    <svg class="page-art" viewBox="0 0 560 860" width="560" height="860">
      <defs>
        <linearGradient id="teamTone" x1="0" y1="0" x2="1" y2="1">
          <stop offset="0" stop-color="#f4f4f5"/>
          <stop offset="0.6" stop-color="#d9d9dc"/>
          <stop offset="1" stop-color="#b9b9be"/>
        </linearGradient>
      </defs>
      <path d="M0 0 H560 V60 C440 190 260 330 0 345 Z" fill="var(--red)"/>
      <path d="M0 0 H560 V40 C440 170 260 310 0 325 Z" fill="var(--white)"/>
      <path role="img" aria-label="Photo of a smiling team of call center representatives wearing headsets" d="M0 0 H560 V20 C440 150 260 290 0 308 Z" fill="url(#teamTone)"/>
    </svg>

    <div class="block about" style="left:16px; top:378px; width:232px;">
      <h2 class="label">About Us:</h2>
      <p>Talbrook, over the past 84 years, has operated through wars, floods and hurricanes. Our long history is important as it shows Consistency, Professionalism, Experience, and a Can Do Attitude, which is hard to find in the answering service industry today.</p>
      <p>At Talbrook, you'll never be just another a number. We will become part of YOUR team on day one and remain there, ready and honored to serve by providing reliable, professional answering services, 24-7-365, as needed.</p>
      <h2 class="label wide">Still Growing? Find a Scalable Phone Answering Service</h2>
      <p>A scalable solution is one that doesn't waste resources when you don't need them, but easily adapts to future growth. All of our services at Talbrook grow with you, meaning you don't pay for additional support until you need it.</p>
    </div>

    <div class="block" style="left:30px; top:784px; width:225px;">
      <p class="contact-heading">Any information:</p>
    </div>
    <div class="web-tab">www.Talbrooksvc.com</div>

    <div class="col-rule" style="left:260px; top:330px; height:500px;"></div>

    <div class="block services" style="left:272px; top:322px; width:272px;">
      <h2 class="label wide">Automated or Live – Answering Services That Work for You</h2>
      <p>Tell us about your needs and your budget and we'll do the rest. Talbrook selects a system that satisfies your basic requirements, then evaluates your business to find a long-term solution that will work for you and your customers.</p>
      <h2 class="label">Live Answering Service</h2>
      <p>Steady Line is more than an answering service, it's an extension of your company. Our professional representatives take pride in being your direct line of communication with existing customers, potential customers and valued business partners. Before we start fielding calls, our representatives are trained according to the details of your business and industry.</p>
      <ul class="ticks">
        <li>24 Hour Answering Service</li>
        <li>Virtual Receptionist / Virtual Assistant</li>
        <li>Live Message Relay</li>
        <li>Help Desk Overflow</li>
        <li>Call Screening</li>
        <li>Bilingual Answering (Spanish Answering Service)</li>
        <li>Automated Services</li>
      </ul>
    </div>
  </section>

  <section class="page page-right">
    <svg class="page-art" viewBox="0 0 560 860" width="560" height="860">
      <defs>
        <linearGradient id="agentTone" x1="0" y1="0" x2="1" y2="1">
          <stop offset="0" stop-color="#f1eeec"/>
          <stop offset="0.5" stop-color="#d8d3d0"/>
          <stop offset="1" stop-color="#8f8a88"/>
        </linearGradient>
      </defs>
      <path d="M170 860 C240 715 390 628 560 598 V860 Z" fill="var(--red)"/>
      <path d="M182 860 C252 726 398 642 560 614 V860 Z" fill="var(--white)"/>
      <path role="img" aria-label="Photo of smiling call center agents with headsets working in a row" d="M192 860 C262 734 404 652 560 626 V860 Z" fill="url(#agentTone)"/>
    </svg>

    <div class="block automated" style="left:14px; top:16px; width:258px;">
      <h2 class="label">Automated Services</h2>
      <p>Live answering services are not necessary for all businesses. Steady Line offers automated answering services as a cost-effective option for continuous customer contact. And just because it's "automated" that doesn't mean it isn't tailored to the specific needs of your business.</p>
      <p>(Live and automated services can be combined for a very cost effective and professional solution.)</p>
      <p>Here are some of the customizable automated solutions we offer for businesses of all sizes:</p>
      <ul class="ticks">
        <li>Voice Mail (with or without extensions/sub-boxes)</li>
        <li>Voice Mail with Operator Revert</li>
        <li>Call Routing &amp; Transfer</li>
        <li>Web Integration</li>
        <li>Database Interaction</li>
        <li>Text Messaging</li>
        <li>Alpha Paging</li>
        <li>Email</li>
        <li>Fax</li>
        <li>Combination Service – Utilize our reliable voice mail system with an operator revert functionality. Your callers have the option of pressing "0" for a representative at any time.</li>
      </ul>
    </div>

    <div class="block call-center" style="left:14px; top:476px; width:258px;">
      <h2 class="label">Call Center Services Done Right</h2>
      <p>Talbrook is a complete call center provider. We train our representatives to follow your business protocol and then they are able to work as an autonomous unit that only requires your attention if you wish to change a procedure. Our call center representatives handle everything from pre-qualification to appointment setting and order taking. The Steady Line team is your team.</p>
      <p class="list-title">Our call center services include:</p>
      <ul class="ticks">
        <li>Order Taking (on your site or our system)</li>
        <li>Pre-Qualification</li>
        <li>Help Desk</li>
        <li>Appointment Setting</li>
        <li>Appointment Confirmation</li>
        <li>Lead Generation</li>
        <li>Order Processing</li>
      </ul>
    </div>

    <div class="col-rule" style="left:283px; top:20px; height:460px;"></div>

    <div class="block special" style="left:296px; top:16px; width:250px;">
      <h2 class="label" style="padding-right:60px;">Special Services</h2>
      <p>Medical Answering Services – Steady Line representatives understand the unique needs of the medical community and are trained to provide the support you need.</p>
      <ul class="ticks" style="margin-top:14px;">
        <li>HIPAA compliant messaging system</li>
        <li>Medical messages stored securely for 1 year</li>
        <li>Disaster Recovery – stay in contact with employees, management and customers in the event of emergency</li>
      </ul>
      <p style="margin-top:40px; margin-bottom:0;">Oil and Gas – We serve many clients in the Energy industry and our representatives are well-versed in handling customer relations in what can be a demanding field.</p>
      <p style="margin-bottom:0;">Commercial Property Management – Our representatives have experience maintaining positive relations with tenants, property managers and other real estate personnel.</p>
      <p>*Ask one of our representatives about custom solutions for your industry</p>
    </div>

    <div class="block test-drive" style="left:302px; top:476px; width:236px;">
      <h2 class="label" style="padding-right:70px;">Test Drive</h2>
      <p>There's no better way to get a feel for our services than by speaking with one of our own representatives – 866.555.LINE.</p>
    </div>
  </section>

</main>
</body>
</html>
```